Every Shelf Set Neatly or ESN Organized needs a business card design. ESN Organized is a professi

We need a business card design that is clean, sharp and conveys a sense of organization. I already have a logo.

Target Market(s)

Families (specifically mothers), small business owners, parents, seniors

Industry/Entity Type

Business

Contact Information for Business Card

My website is www.esnorganized-example.com and my Facebook page is http://www.sociallink-example.com/everyshelfsetneatly. The phone number is 418-552-7094 and I want to be listed as Lorna M. Pelham, Owner

Requirements
Must have
• My logo.

```html
<!DOCTYPE html>
<html lang="en">
<head>
<meta charset="utf-8">
<title>ESN Organized — Business Card</title>
<link rel="stylesheet" href="https://fonts.googleapis.com/css2?family=Arimo:wght@400;700&family=Montserrat:wght@400&display=swap">
<style>
  :root {
    --backdrop: #3a3b3d;
    --card-white: #ffffff;
    --card-black: #0b0b0c;
    --brand-blue: #2f8de4;
    --brand-blue-deep: #1f74c9;
    --brand-blue-light: #5aa8ee;
    --ink-dark: #2a2a2c;
    --ink-light: #d9d9d9;
    --ink-white: #ffffff;
  }
  * { box-sizing: border-box; margin: 0; padding: 0; }
  html, body {
    width: 1200px; height: 950px; overflow: hidden;
    background: var(--backdrop);
    font-family: "Arimo", Arial, sans-serif;
  }
  .canvas {
    width: 1200px; height: 950px;
    display: flex; flex-direction: column; align-items: center; justify-content: center;
    gap: 50px;
  }
  .card {
    width: 700px; height: 400px; border-radius: 6px;
    position: relative; overflow: hidden;
    box-shadow: 0 12px 30px rgba(0,0,0,.45);
  }
  .card--front { background: var(--card-white); }
  .card--back { background: var(--card-black); display: flex; flex-direction: column; align-items: center; justify-content: center; gap: 22px; }

  .brand {
    display: flex; align-items: center; gap: 14px;
    font-family: "Montserrat", "Arimo", sans-serif; font-weight: 400;
    letter-spacing: .12em; text-transform: uppercase;
  }
  .brand__mark { width: 22px; height: 22px; border-radius: 50%; }
  .brand__name { font-size: 30px; }

  .card--front .brand { position: absolute; top: 62px; left: 0; right: 0; justify-content: center; color: var(--ink-dark); }
  .card--front .brand__mark { background: var(--brand-blue); }

  .card--back .brand { color: var(--ink-light); }
  .card--back .brand__mark { background: var(--ink-light); }
  .back-url { color: var(--ink-light); font-size: 18px; letter-spacing: .14em; }

  .contact-band {
    position: absolute; left: 24px; right: 24px; top: 150px; height: 210px;
    border-radius: 105px;
    background: linear-gradient(180deg, var(--brand-blue-light) 0%, var(--brand-blue) 45%, var(--brand-blue-deep) 100%);
    color: var(--ink-white);
    display: flex; flex-direction: column; align-items: center; justify-content: center;
    text-align: center;
  }
  .contact__name { font-weight: 700; font-size: 26px; }
  .contact__rule { width: 300px; height: 1px; background: rgba(255,255,255,.55); margin: 8px 0; }
  .contact__title { font-size: 17px; }
  .contact__lines { margin-top: 14px; font-size: 18px; line-height: 1.5; }
  .contact__label { font-weight: 700; }
  .contact__row { display: flex; align-items: center; justify-content: center; gap: 8px; }
  .contact__gap { display: inline-block; width: 18px; }
  .social-square { width: 15px; height: 15px; background: var(--ink-white); border-radius: 2px; }
</style>
</head>
<body>
<main class="canvas">
  <section class="card card--front" aria-label="Business card front">
    <div class="brand">
      <span class="brand__mark"></span>
      <span class="brand__name">Every Shelf Set Neatly</span>
    </div>
    <div class="contact-band">
      <p class="contact__name">Lorna M. Pelham</p>
      <div class="contact__rule"></div>
      <p class="contact__title">Owner</p>
      <div class="contact__lines">
        <p><span class="contact__label">Phone:</span> 418-552-7094<span class="contact__gap"></span><span class="contact__label">Web:</span> www.esnorganized-example.com</p>
        <p class="contact__row"><span class="social-square"></span>everyshelfsetneatly</p>
      </div>
    </div>
  </section>

  <section class="card card--back" aria-label="Business card back">
    <div class="brand">
      <span class="brand__mark"></span>
      <span class="brand__name">Every Shelf Set Neatly</span>
    </div>
    <p class="back-url">esnorganized-example.com</p>
  </section>
</main>
</body>
</html>
```